Mobile Repair Service on location needs a Web Design

We are starting a new mobile device repair service called Handset Haven and our website needs a design!

Hello Designers!
First, we'd like to make clear this is more than a simple web design contest, we want the designers to create an idea. We want someone who can create the whole theme of the service's we provide. We want someone that can help design our visual branding, help us communicate a sentiment. And we are willing to pay for that.

Who are we?
Our company is based in Rotterdam, the Netherlands. We provide different services for all kinds of electronic devices. The kind of services we provide are, among other things, installations of hardware and software and the repair of broken or malfunctioning devices.
We are starting a new service that offers mobile device repairs on location, be it at the home of our customers, their office, or any other place. Just give us the address and we will come to you for the repair job. This is also our main USP. We have multiple skilled engineers who drive trough the country on a daily basis and can be on location within a working day. Repair is done immediately onsite while the customer waits. At this stage we will start with the smartphone product-group within the mobile devices. In a second phase we might also add tablets.
People don't want to be without their phone for weeks because of some parts that needed to be ordered by a repair center they had to sent their phone to. We offer a fully functional mobile repair center in the form of specially customized vans. These vans have all the tools and utilities needed by our engineers to safely repair your mobile device. Your phone is being repaired directly in front of you, the next business-day, on a location you desire.

For this new service we are creating a website called Handset Haven. The website needs a story and matching design and this is where you come in. We are not looking for a simple template design we can get from any place. We need a story. We want you to create an idea, build a unique theme or vision that helps sell the product/service. This goes beyond the design of the website. We need the whole package, the design you are creating needs to have returning elements like icons, color use, images, maybe even characters etc. You name it! There needs to be a common thread in the design so we can reuse elements in, for example, the email templates, the work order or receipt we give to our customers (we may contact the winner of the contest to design these for us as well!).

The name 'Handset Haven' is chosen. Rehab (short for rehabilitate) has a bold and playful tone to it and the design needs to reflect the name. So we're looking for a somewhat playful and cheeky design. Definitely not too serious and definitely modern. We already got a logo that we love and that fit's this description (see attached design documents for the logo). It's bold, powerful and fun. Our web design needs to reflect this as well and has to fit in with our logo.
We would really like it if the design somehow incorporates elements that highlight our unique selling points (repairs on location, we come to you etc.). We would really like some form of story telling in the design. Think clumsy people breaking their phones. Teenagers in tears because they have no access to their friends. People nowadays have the need to always be 'connected'. What happens when your phone is broken or malfunctioning? We're handling tech, we are nerds and a little bit weird, but we're professionals and here to help you with your problem. The sentiment Byte Brigade tries to communicate is something we really like. We're looking for fresh idea's, anything goes!

In an overview all Unique Selling Points of the Handset haven service:
- Professional service on location. Don’t ship to us we will come to you!
- Clear pricing upfront. No hidden cost.
- Next business-day repair.
- Backed by a professional call center open 12 hours a day and open on a Saturday as well
- Backed by a professional repair center with more then 12 years of experience
- Repair is done by certified engineers
- 1 year warranty on the repair

The process:
The main function of our website will be for customers to make a repair request. A customer will visit our website and can make a repair request immediately by going through a 'request-order-flow'. In this flow he or she will need to fill in some forms and can select wich type/model/brand of mobile device he or she has and what parts need to be repaired. After a request is placed we will call the customer back (within an hour) for a short intake and to set a date/time and location. Our engineer will meet the customer at the specified location and will repair the device onsite in one of our mobile repair centers, which is a specialized van equipped with all the tools needed for device restorations.
So in short the steps are:
- Choose your device and repair job
- Place the order
- Get a callback within the hour
- Set date and location
- We will come to you.

Website functionality:
Our website is our main form of communication. So the sentiment we want to communicate needs be reflected in the design. We need a main/front page designed (preferably a long scrolling page design) containing:
1. Customers will be able to request a repair job directly on our website. So there will need to be a prominent button/link at the top of our main page that will bring the customer to this 'request-order-flow'. This is the main flow which needs to be full focus on the front page. All other items are secondary.
2. The general information of who we are and what we do, and why the customer should choose us. Preferably in short bullet-point type keywords/sentences with icons or other visual cues. See our unique selling points to get an idea of the information that will be displayed here.
3. There needs to be a section that will explain the process (see above) of a repair request step-by- step, again in brief short key sentences and with (custom) icons.
4. There needs to be a section that explains to the customer he/she can always contact us if they are not sure what the problem is with their device, and for this reason are not sure what repair request they should order.
5. We want to implement some functionality that display customer ratings or customer reviews. So there needs to be room for some kind of widget of plugin we're going to implement which shows these reviews.
6. A 'For business section' where we will explain all the options we provide for corporate clients.
7. Social media links.
8. There needs to be a menu with buttons that leads to the all sections described in the previous points.

For now, we need a design for our front page. In the second phase, when we have picked our winner, we may ask the winner to design the page(s) for our request workflow as well.

EDIT:
Finally, we have a very specific order in mind for the different segments of our website. We would like you to add some more segments that were not in our original brief as well:

1. Top header with order/request button. (should instantly make clear our main USP, we do repairs on location)
2. Our process
3. Our unique selling points / why choose us
4. The kind of repairs we do (broken screens, broken batteries, water damage, broken camera's, no sound etc.)
5. A 'meet our team' section, where we introduce some of our engineers
6. A 'contact us for any questions' section/
7. Testimonials/user reviews
8. A section where we show key performance indicators
9. 'For businesses' sections
10.'Subscribe for newsletter' field
11. Social media buttons

Industry/Entity Type

It Service

Number of Pages Required

1 page

Font styles to use
Sans Serif

Requirements
Must have
• a main/front page, design only
• custom icons/images for banners, adverts online and in print (high res)
Nice to have
• Storytelling in our design.
• Design that fits with our brand new logo.
• Elements like icons to have a flat design.
• Keep in mind that the website will need to be responsive when designing! (Ideally provide an example of the mobile design as well)
• Create a fun and trustworthy feeling.

```html
<!DOCTYPE html>
<html lang="en">
<head>
<meta charset="utf-8">
<title>Handset Haven – Mobile Repair On Location</title>
<link href="https://fonts.googleapis.com/css2?family=Open+Sans:wght@400;600;700;800&display=swap" rel="stylesheet">
<style>
:root{
  --orange:#f06a2a;
  --orange-dark:#e35d1f;
  --lavender:#c4bfe4;
  --lavender-line:#b9b2e0;
  --ink:#2b2b2b;
  --text:#555;
  --nav:#333;
  --cream:#fcfadf;
  --grey:#f1f1f1;
  --footer:#f3f3f3;
  --white:#fff;
}
*{box-sizing:border-box;margin:0;padding:0}
html,body{width:1200px;height:3291px;overflow:hidden}
body{font-family:'Open Sans',Arial,sans-serif;color:var(--text);background:var(--white);position:relative}
.btn{display:inline-block;background:var(--lavender);color:var(--ink);font-weight:700;font-size:14px;letter-spacing:.5px;text-transform:uppercase;padding:0 34px;line-height:52px;height:52px}

/* header */
.site-header{position:absolute;top:0;left:0;width:1200px;height:114px}
.brand{position:absolute;left:79px;top:28px;display:flex;align-items:center;gap:12px}
.brand-dot{width:46px;height:46px;border-radius:50%;background:var(--orange)}
.brand-name{font-weight:800;font-size:18px;line-height:20px;color:var(--nav);text-transform:uppercase}
.brand-name small{display:block;font-size:8px;line-height:12px;font-weight:600;text-transform:none;color:var(--nav)}
.header-contact{position:absolute;left:890px;top:16px}
.header-contact div{display:flex;align-items:center;gap:14px;height:40px;font-size:15px}
.header-contact .ico{width:26px;height:26px;border-radius:50%;background:var(--lavender);display:flex;align-items:center;justify-content:center}
.header-contact .phone{color:var(--orange);font-weight:700;font-size:19px}
.main-nav{position:absolute;top:114px;left:0;width:1200px;height:46px;background:var(--nav);display:flex;padding-left:75px}
.main-nav a{color:#fff;font-size:13px;font-weight:700;text-transform:uppercase;line-height:46px;padding:0 23px;text-decoration:none}
.main-nav a.active{background:var(--orange)}

/* hero */
.hero{position:absolute;top:160px;left:0;width:1200px;height:503px;overflow:hidden}
.hero-photo{position:absolute;inset:0;background:
  radial-gradient(ellipse 340px 260px at 930px 330px,rgba(236,214,196,.85),rgba(236,214,196,0) 70%),
  radial-gradient(ellipse 260px 320px at 1060px 120px,rgba(120,86,64,.75),rgba(120,86,64,0) 70%),
  linear-gradient(90deg,#7f7166 0%,#918174 35%,#ab9a89 60%,#c8b7a3 78%,#8d7663 100%)}
.hero-copy{position:absolute;left:75px;top:106px;color:#fff}
.hero-copy h1{font-size:58px;font-weight:800;letter-spacing:1px;line-height:64px}
.hero-copy .tagline{font-size:30px;font-style:italic;font-weight:700;margin-top:2px}
.hero-copy .lead{font-size:22px;font-weight:700;line-height:30px;margin-top:14px;width:460px}
.hero-copy .btn{margin-top:34px}
.hero-dots{position:absolute;left:75px;top:434px;display:flex;gap:8px}
.hero-dots span{width:13px;height:13px;border-radius:50%;background:#fff}
.hero-dots span:first-child{background:var(--orange)}

/* split sections */
.split{position:absolute;left:0;width:1200px;display:flex}
.split .art{width:600px;height:100%}
.welcome .art{background:
  radial-gradient(ellipse 120px 190px at 170px 230px,rgba(90,90,90,.55),rgba(90,90,90,0) 75%),
  radial-gradient(ellipse 110px 160px at 440px 260px,rgba(240,130,60,.45),rgba(240,130,60,0) 75%),
  var(--cream)}
.who .art{background:
  radial-gradient(ellipse 130px 190px at 300px 230px,rgba(90,90,90,.55),rgba(90,90,90,0) 75%),
  radial-gradient(ellipse 90px 170px at 120px 200px,rgba(240,130,60,.4),rgba(240,130,60,0) 75%),
  radial-gradient(ellipse 80px 140px at 460px 250px,rgba(240,130,60,.4),rgba(240,130,60,0) 75%),
  var(--cream)}
.split .copy{width:600px;height:100%;padding:68px 75px 0 75px}
.section-title{display:flex;align-items:center;gap:14px;font-size:25px;font-weight:700;color:var(--ink);text-transform:uppercase}
.section-title .mark{width:40px;height:40px;border-radius:50%;background:var(--orange)}
.copy p{font-size:14px;line-height:28px;margin-top:26px}
.copy .btn{margin-top:34px}
.welcome{top:663px;height:430px}
.who{top:1093px;height:432px}
.who .copy{padding-left:58px}

/* usp */
.usp{position:absolute;top:1525px;left:0;width:1200px;height:450px;background:linear-gradient(90deg,#ee6426,#f16d2d 50%,#ee6426);color:#fff}
.usp h2{text-align:center;font-size:32px;font-weight:700;padding-top:40px}
.usp-list{position:absolute;top:120px;left:77px;width:1060px;display:grid;grid-template-columns:537px 523px}
.usp-list ul{list-style:none}
.usp-list li{position:relative;padding-left:26px;font-size:14.5px;line-height:23px;margin-bottom:11px}
.usp-list li:before{content:"";position:absolute;left:0;top:5px;width:13px;height:13px;border-radius:50%;background:#fff}
.usp-list li:after{content:"";position:absolute;left:4px;top:7px;width:4px;height:6px;border:solid var(--orange);border-width:0 2px 2px 0;transform:rotate(45deg)}
.usp .btn{position:absolute;left:524px;top:335px;padding:0 20px}

/* process */
.process{position:absolute;top:1975px;left:0;width:1200px;height:373px}
.process h2{text-align:center;font-size:27px;font-weight:700;color:var(--ink);padding-top:50px}
.steps{position:absolute;top:128px;left:90px;width:1040px;display:flex;justify-content:space-between}
.step{width:170px;text-align:center}
.step svg{display:block;margin:0 auto}
.step p{font-size:16px;font-weight:600;color:var(--ink);line-height:22px;margin-top:12px}
.step-arrow{position:absolute;top:48px}

/* testimonials */
.testimonials{position:absolute;top:2348px;left:0;width:1200px;height:401px;background:var(--grey)}
.testimonials h2{position:absolute;left:77px;top:50px;font-size:27px;font-weight:700;color:var(--ink)}
.quote{position:absolute;top:118px;width:270px;font-size:14px;font-style:italic;line-height:27px}
.reviewer{display:flex;align-items:center;gap:14px;margin-top:30px;font-style:normal}
.reviewer .avatar{width:64px;height:64px;border-radius:50%;background:linear-gradient(#c9b49e,#6a5a4d)}
.reviewer b{display:block;color:var(--orange);font-size:13px;text-transform:uppercase;line-height:18px}
.reviewer span{font-size:13px;line-height:18px}
.testimonial-photo{position:absolute;left:689px;top:0;width:511px;height:401px;background:
  radial-gradient(ellipse 150px 180px at 230px 110px,rgba(110,78,60,.6),rgba(110,78,60,0) 75%),
  radial-gradient(ellipse 200px 140px at 240px 330px,rgba(60,60,70,.35),rgba(60,60,70,0) 75%),
  linear-gradient(135deg,#ebe8e5 0%,#dcd3cc 55%,#c9b3a3 100%)}

/* newsletter */
.newsletter{position:absolute;top:2749px;left:0;width:1200px;height:263px;text-align:center}
.newsletter h2{font-size:27px;font-weight:700;color:var(--ink);padding-top:50px;text-transform:uppercase}
.newsletter p{font-size:15px;margin-top:12px}
.signup{position:absolute;top:160px;left:274px;display:flex;gap:13px}
.signup .field{width:474px;height:51px;border:1px solid #d6d6d6;display:flex;align-items:center;gap:14px;padding-left:18px;font-size:14px;color:#999}
.signup .btn{height:51px;line-height:51px;width:165px;padding:0;text-align:center}

/* footer */
.site-footer{position:absolute;top:3012px;left:0;width:1200px;height:279px;background:var(--footer)}
.site-footer .brand{left:77px;top:54px}
.site-footer .brand-dot{background:#9a9a9a}
.socials{position:absolute;left:77px;top:144px;display:flex;gap:14px}
.socials span{width:22px;height:22px;border-radius:50%;background:var(--nav)}
.copyright{position:absolute;left:77px;top:188px;font-size:12px;line-height:20px}
.foot-col{position:absolute;top:50px}
.foot-col h4{color:var(--orange);font-size:14px;font-weight:700;text-transform:uppercase;margin-bottom:14px}
.foot-col ul{list-style:none}
.foot-col li{font-size:13px;line-height:32px}
.foot-col .contact li{display:flex;gap:10px;line-height:26px}
</style>
</head>
<body>

<header class="site-header">
  <div class="brand"><span class="brand-dot"></span><span class="brand-name">Handset<br>Haven<small>We will come to you!</small></span></div>
  <div class="header-contact">
    <div><span class="ico"><svg width="13" height="13" viewBox="0 0 24 24"><path fill="#fff" d="M6.6 10.8a15 15 0 0 0 6.6 6.6l2.2-2.2c.3-.3.7-.4 1-.2 1.1.4 2.3.6 3.6.6.6 0 1 .4 1 1V20c0 .6-.4 1-1 1C10.6 21 3 13.4 3 4c0-.6.4-1 1-1h3.5c.6 0 1 .4 1 1 0 1.3.2 2.5.6 3.6.1.3 0 .7-.2 1z"/></svg></span><span class="phone">1-800-555-0147</span></div>
    <div><span class="ico"><svg width="13" height="13" viewBox="0 0 24 24"><path fill="#fff" d="M2 5h20v14H2z M2 5l10 8 10-8" stroke="#c4bfe4" stroke-width="1.5"/></svg></span><span>hello@handsethaven.example</span></div>
  </div>
</header>
<nav class="main-nav">
  <a class="active">Home</a><a>About Us</a><a>Services</a><a>Our USP</a><a>Our Process</a><a>Testimonials</a><a>Blog</a><a>Careers</a><a>Contact Us</a>
</nav>

<section class="hero">
  <div class="hero-photo" role="img" aria-label="Photo of a technician examining a smartphone with a cracked screen"></div>
  <div class="hero-copy">
    <h1>HANDSET HAVEN</h1>
    <div class="tagline">We will come to you!</div>
    <div class="lead">Vestibulum ante ipsum primis in faucibus orci luctus et ultrices posuere..</div>
    <a class="btn">Read More</a>
  </div>
  <div class="hero-dots"><span></span><span></span><span></span><span></span></div>
</section>

<section class="split welcome">
  <div class="copy">
    <h2 class="section-title"><span class="mark"></span>Welcome to Handset Haven</h2>
    <p>Aliquam molestie, mi et imperdiet euismod, dui purus auctor tellus, et interdum lacus lectus et ante. Sed accumsan sollicitudin sapien, sit amet adipiscing turpis gravida ac. In congue, neque ac lobortis volutpat, libero mauris varius mi, vitae suscipit ipsum ligula vitae risus. Duis aliquam nibh a dui iaculis viverra id a velit.</p>
    <a class="btn">Read More</a>
  </div>
  <div class="art" role="img" aria-label="Cartoon of a cracked smartphone character running from a repair engineer carrying a toolbox"></div>
</section>

<section class="split who">
  <div class="art" role="img" aria-label="Cartoon of two engineers repairing a sitting cracked smartphone with giant screwdrivers"></div>
  <div class="copy">
    <h2 class="section-title"><span class="mark"></span>Who are we?</h2>
    <p>Our company is based in Rotterdam, the Netherlands. We provide different services for all kinds of electronic devices. The kind of services we provide are, among other things, installations of hardware and software and the repair of broken or malfunctioning devices.</p>
    <a class="btn">Read More</a>
  </div>
</section>

<section class="usp">
  <h2>OUR USP</h2>
  <div class="usp-list">
    <ul>
      <li>Professional service on location. Don't ship to us we will &nbsp;come<br>to you!</li>
      <li>Clear pricing upfront. No hidden cost.</li>
      <li>Next business-day repair.</li>
      <li>Backed by a professional call center open 12 hours a day and<br>open on a Saturday as well.</li>
    </ul>
    <ul>
      <li>Backed by a professional repair center with more then 12 years<br>of experience.</li>
      <li>Repair is done by certified engineers.</li>
      <li>1 year warranty on the repair.</li>
    </ul>
  </div>
  <a class="btn">Repair Request</a>
</section>

<section class="process">
  <h2>OUR PROCESS</h2>
  <div class="steps">
    <div class="step">
      <svg width="110" height="120" viewBox="0 0 110 120"><path d="M55 6 L100 22 V60 C100 88 78 106 55 114 C32 106 10 88 10 60 V22 Z" fill="none" stroke="#b9b2e0" stroke-width="3"/><rect x="44" y="38" width="22" height="38" rx="3" fill="none" stroke="#f06a2a" stroke-width="3"/><circle cx="55" cy="70" r="2" fill="#f06a2a"/></svg>
      <p>Choose your device and repair job</p>
    </div>
    <div class="step">
      <svg width="110" height="120" viewBox="0 0 110 120"><path d="M55 6 L100 22 V60 C100 88 78 106 55 114 C32 106 10 88 10 60 V22 Z" fill="none" stroke="#b9b2e0" stroke-width="3"/><rect x="38" y="40" width="32" height="32" rx="3" fill="none" stroke="#f06a2a" stroke-width="3"/><path d="M50 62 L70 42 L76 48 L56 68 L48 70 Z" fill="#f06a2a"/></svg>
      <p>Place the<br>order</p>
    </div>
    <div class="step">
      <svg width="110" height="120" viewBox="0 0 110 120"><path d="M55 6 L100 22 V60 C100 88 78 106 55 114 C32 106 10 88 10 60 V22 Z" fill="none" stroke="#b9b2e0" stroke-width="3"/><path transform="translate(37 38) scale(1.5)" fill="#f06a2a" d="M6.6 10.8a15 15 0 0 0 6.6 6.6l2.2-2.2c.3-.3.7-.4 1-.2 1.1.4 2.3.6 3.6.6.6 0 1 .4 1 1V20c0 .6-.4 1-1 1C10.6 21 3 13.4 3 4c0-.6.4-1 1-1h3.5c.6 0 1 .4 1 1 0 1.3.2 2.5.6 3.6.1.3 0 .7-.2 1z"/></svg>
      <p>Get a callback<br>within the hour</p>
    </div>
    <div class="step">
      <svg width="110" height="120" viewBox="0 0 110 120"><path d="M55 6 L100 22 V60 C100 88 78 106 55 114 C32 106 10 88 10 60 V22 Z" fill="none" stroke="#b9b2e0" stroke-width="3"/><rect x="38" y="42" width="34" height="32" rx="3" fill="none" stroke="#f06a2a" stroke-width="3"/><path d="M38 51 H72 M46 37 V46 M64 37 V46" stroke="#f06a2a" stroke-width="3"/><g fill="#f06a2a"><rect x="43" y="56" width="5" height="5"/><rect x="52" y="56" width="5" height="5"/><rect x="61" y="56" width="5" height="5"/><rect x="43" y="64" width="5" height="5"/><rect x="52" y="64" width="5" height="5"/></g></svg>
      <p>Set date and<br>location</p>
    </div>
    <div class="step">
      <svg width="110" height="120" viewBox="0 0 110 120"><path d="M55 6 L100 22 V60 C100 88 78 106 55 114 C32 106 10 88 10 60 V22 Z" fill="none" stroke="#b9b2e0" stroke-width="3"/><g fill="#f06a2a"><circle cx="55" cy="47" r="7"/><circle cx="41" cy="52" r="5"/><circle cx="69" cy="52" r="5"/><path d="M43 72 C43 60 67 60 67 72 Z"/><path d="M31 70 C31 61 44 60 45 64 L42 70 Z"/><path d="M79 70 C79 61 66 60 65 64 L68 70 Z"/></g></svg>
      <p>We will come<br>to you</p>
    </div>
    <svg class="step-arrow" style="left:165px" width="50" height="30" viewBox="0 0 50 30"><path d="M2 22 C14 10 30 8 40 12 L38 4 L48 15 L36 24 L38 17 C28 14 16 16 2 22Z" fill="#e4e4e4"/></svg>
    <svg class="step-arrow" style="left:374px" width="50" height="30" viewBox="0 0 50 30"><path d="M2 22 C14 10 30 8 40 12 L38 4 L48 15 L36 24 L38 17 C28 14 16 16 2 22Z" fill="#e4e4e4"/></svg>
    <svg class="step-arrow" style="left:582px" width="50" height="30" viewBox="0 0 50 30"><path d="M2 22 C14 10 30 8 40 12 L38 4 L48 15 L36 24 L38 17 C28 14 16 16 2 22Z" fill="#e4e4e4"/></svg>
    <svg class="step-arrow" style="left:790px" width="50" height="30" viewBox="0 0 50 30"><path d="M2 22 C14 10 30 8 40 12 L38 4 L48 15 L36 24 L38 17 C28 14 16 16 2 22Z" fill="#e4e4e4"/></svg>
  </div>
</section>

<section class="testimonials">
  <h2>WHAT OUR CUSTOMERS HAVE TO SAY</h2>
  <div class="quote" style="left:77px">“ Aliquam molestie, mi et imperdiet euismod, dui purus auctor tellus, et interdum lacus lectus et ante. Sed accumsan sollicitudin sapien, sit amet adipiscing..”
    <div class="reviewer"><span class="avatar" role="img" aria-label="Customer portrait"></span><div><b>Name Heading</b><span>Location</span></div></div>
  </div>
  <div class="quote" style="left:390px">“ Aliquam molestie, mi et imperdiet euismod, dui purus auctor tellus, et interdum lacus lectus et ante. Sed accumsan sollicitudin sapien, sit amet adipiscing..”
    <div class="reviewer"><span class="avatar" role="img" aria-label="Customer portrait"></span><div><b>Name Heading</b><span>Location</span></div></div>
  </div>
  <div class="testimonial-photo" role="img" aria-label="Photo of a smiling customer holding a smartphone and pointing at it"></div>
</section>

<section class="newsletter">
  <h2>Newsletter Sign Up</h2>
  <p>Aliquam molestie, mi et imperdiet euismod, dui purus auctor tellus, et interdum lacus lectus et ante.</p>
  <div class="signup">
    <div class="field"><svg width="16" height="12" viewBox="0 0 16 12"><rect x="0.5" y="0.5" width="15" height="11" fill="none" stroke="#f06a2a"/><path d="M.5 .5 L8 7 L15.5 .5" fill="none" stroke="#f06a2a"/></svg>Enter Email Address</div>
    <a class="btn">Subscribe</a>
  </div>
</section>

<footer class="site-footer">
  <div class="brand"><span class="brand-dot"></span><span class="brand-name" style="color:#777">Handset<br>Haven<small style="color:#777">We will come to you!</small></span></div>
  <div class="socials" aria-label="Social media links"><span></span><span></span><span></span><span></span><span></span></div>
  <div class="copyright">Copyright © 2017 All Right Reserved<br>Terms Of Services</div>
  <div class="foot-col" style="left:373px"><h4>Site Map</h4><ul><li>Home</li><li>About Us</li><li>Services</li><li>Our USP</li><li>Our Process</li></ul></div>
  <div class="foot-col" style="left:489px;top:82px"><ul style="margin-top:-4px"><li>Testimonials</li><li>Blog</li><li>Careers</li><li>Contact Us</li></ul></div>
  <div class="foot-col" style="left:643px"><h4>Support &amp; Services</h4><ul><li>Customer Service</li><li>Protection Plans</li><li>Schedule a Service</li><li>Trade-In Program</li><li>More Support &amp; Services</li></ul></div>
  <div class="foot-col" style="left:884px"><h4>Contact Info</h4><ul class="contact"><li>1450 Harbor Lane,<br>Leeds, LS1 4QT</li><li><span style="color:#333">&#9742;</span>1-800-555-0147</li><li><span style="color:#333">&#9993;</span>hello@handsethaven.example</li></ul></div>
</footer>

</body>
</html>
```